Need Business Card for our Real Estate Business with Sales Executive's Picture

PANTONE 484 C ( RED)

PANTONE 2766 C ( BLUE

Industry/Entity Type

Real Estate

Contact Information for Business Card

Name, Mobile, email, & picture of Person
Agency Phone, address, Web address

Requirements
Must have
• Our Logo Colours, Agent Picture,

```html
<!DOCTYPE html>
<html lang="en">
<head>
<meta charset="utf-8">
<title>Alder Real Estate – Business Card</title>
<link href="https://fonts.googleapis.com/css2?family=Ubuntu:wght@400;500&display=swap" rel="stylesheet">
<style>
  :root {
    --page-bg: #e6e2dd;
    --card-light: #eeebe7;
    --navy: #1c2e5c;
    --navy-deep: #141f45;
    --brand-red: #9a3324;
    --icon-red: #b8433a;
    --text-light: #f1ede6;
    --text-soft: #d9dbe4;
  }
  * { box-sizing: border-box; margin: 0; padding: 0; }
  html, body {
    width: 1200px;
    height: 1054px;
    overflow: hidden;
    background: var(--page-bg);
    font-family: "Ubuntu", sans-serif;
  }
  .business-card {
    position: absolute;
    left: 100px;
    top: 242px;
    width: 1000px;
    height: 570px;
    background: var(--card-light);
    overflow: hidden;
    box-shadow: 0 10px 30px rgba(0,0,0,0.18);
  }
  .navy-panel {
    position: absolute;
    inset: 0;
    width: 1000px;
    height: 570px;
  }
  .agent-photo {
    position: absolute;
    left: 700px;
    top: 216px;
    width: 300px;
    height: 354px;
    background: linear-gradient(180deg, #c9b8a6 0%, #a98f7a 45%, #2a3d72 75%, #1c2e5c 100%);
  }
  .agent-name {
    position: absolute;
    left: 53px;
    top: 66px;
    font-size: 33px;
    font-weight: 500;
    color: var(--text-light);
  }
  .agent-title {
    position: absolute;
    left: 53px;
    top: 110px;
    font-size: 24px;
    font-weight: 400;
    color: var(--text-light);
  }
  .brand {
    position: absolute;
    left: 560px;
    top: 108px;
    display: flex;
    align-items: center;
    gap: 14px;
  }
  .brand-mark {
    width: 16px;
    height: 16px;
    background: var(--brand-red);
  }
  .brand-name {
    font-size: 40px;
    font-weight: 500;
    color: var(--navy);
    letter-spacing: 1px;
  }
  .contact-list {
    position: absolute;
    left: 60px;
    top: 352px;
    list-style: none;
  }
  .contact-item {
    display: flex;
    align-items: flex-start;
    height: 34px;
    font-size: 24px;
    color: var(--text-soft);
  }
  .contact-item svg {
    width: 20px;
    height: 20px;
    margin-top: 5px;
    margin-right: 16px;
    flex: none;
  }
  .contact-item.address { height: auto; line-height: 34px; }
  .contact-item.address svg { margin-top: 7px; }
</style>
</head>
<body>
  <div class="business-card">
    <svg class="navy-panel" viewBox="0 0 1000 570">
      <defs>
        <linearGradient id="navyFade" x1="0" y1="0" x2="1" y2="1">
          <stop offset="0" stop-color="#22376b"/>
          <stop offset="1" stop-color="#141f45"/>
        </linearGradient>
      </defs>
      <polygon points="0,0 418,0 690,570 0,570" fill="url(#navyFade)"/>
    </svg>

    <div class="agent-photo" role="img" aria-label="Portrait photo of the sales executive in a navy suit and striped tie"></div>

    <div class="brand">
      <span class="brand-mark"></span>
      <span class="brand-name">ALDER REAL ESTATE</span>
    </div>

    <h1 class="agent-name">Dana Whitfield</h1>
    <p class="agent-title">Managing Director</p>

    <ul class="contact-list">
      <li class="contact-item">
        <svg viewBox="0 0 20 20" fill="none" stroke="var(--icon-red)" stroke-width="2"><rect x="5" y="1" width="10" height="18" rx="2"/><line x1="8" y1="16" x2="12" y2="16"/></svg>
        555.201.4830
      </li>
      <li class="contact-item">
        <svg viewBox="0 0 20 20" fill="var(--icon-red)"><path d="M2 7c0-3 4-4 8-4s8 1 8 4v2h-4V7H6v2H2z"/><rect x="4" y="10" width="12" height="8" rx="1"/></svg>
        555-374-9162
      </li>
      <li class="contact-item">
        <svg viewBox="0 0 20 20" fill="var(--icon-red)"><rect x="1" y="4" width="18" height="12" rx="1"/><path d="M1 5l9 6 9-6" fill="none" stroke="#1c2e5c" stroke-width="1.5"/></svg>
        dwhitfield@alderhomes.com
      </li>
      <li class="contact-item">
        <svg viewBox="0 0 20 20" fill="none" stroke="var(--icon-red)" stroke-width="1.6"><circle cx="10" cy="10" r="8"/><ellipse cx="10" cy="10" rx="3.5" ry="8"/><line x1="2" y1="10" x2="18" y2="10"/></svg>
        www.alderhomes.com
      </li>
      <li class="contact-item address">
        <svg viewBox="0 0 20 20" fill="var(--icon-red)"><path d="M10 1a6 6 0 0 0-6 6c0 5 6 12 6 12s6-7 6-12a6 6 0 0 0-6-6zm0 8.5A2.5 2.5 0 1 1 10 4.5a2.5 2.5 0 0 1 0 5z"/></svg>
        <span>418 Garnet Ave #2210,<br>Brookfield, CO 80499</span>
      </li>
    </ul>
  </div>
</body>
</html>
```